Blue Fern Handcrafted Tomato Ketchup packaging design modern

From the best ingredients there is the best ketchup Blue Handcrafted ketchup are specially formulated for fine dining and drinks, bringing out all the flavors. As the Blue Fern handcrafted ketchup is otherwise fabulous: Made with wholesome, fully ripe fruits Nothing with half things! All Blue Fern handcrafted ketchups are pure nature, without any artificial diluents or concentrates. Where tomato is on it, that's all there is to it - guaranteed! the design should be professional and noble despite being trendy. A watcher wants to sell the ketchup as merchandising from our restaurant. but as a single brand positioning. The ketchup is vegan. Dimensions: 6.8 cm Height: 7.8 cm Circumference: 21.6 cm The text down (Text 1-4). The lid of the text the glass packaging is black! Thanks for your efforts. I look forward to your designs.

Target Market(s)

foodies

Font styles to use
Serif
Sans Serif

Colors

Designer to choose colors to be used in the design.

Requirements
Must have
• Title: (Handcrafted Tomato Ketchup) Text One: (Store chilled after opening and consume quickly, pasteurized.) Text Two: (Handcrafted in Switzerland by Varentoli Kulina GmbH, Chur www.bluefern-vorel.example) Text Tree: (Tomatoes, White Wine Vinegar, Aceto Balsamico, Brown Cane Sugar, Corn Starch, Spices, Salt) Text For: (200 grams) or (200g) The Logo of Blue Fern with the Pasta and Wine have to because of the gesety.
Nice to have
• small vegan icon (maybe)
Should not have
• text of the logo (pasta & wine)

```html
<!DOCTYPE html>
<html lang="de">
<head>
<meta charset="utf-8">
<title>Blue Fern – Handcrafted Tomato Ketchup Label</title>
<link rel="stylesheet" href="https://fonts.googleapis.com/css2?family=Josefin+Slab:wght@400;600&family=Archivo+Black&family=Alfa+Slab+One&display=swap">
<style>
  :root {
    --cream: #e6dcc7;
    --tomato: #ee4758;
    --ink: #1d1a1a;
    --font-text: "Josefin Slab", Georgia, serif;
    --font-title: "Archivo Black", "Arial Black", sans-serif;
    --font-label: "Alfa Slab One", Georgia, serif;
  }
  * { box-sizing: border-box; margin: 0; padding: 0; }
  html, body { width: 1200px; height: 434px; overflow: hidden; background: var(--cream); }
  .label { position: relative; width: 1200px; height: 434px; background: var(--cream); color: var(--ink); overflow: hidden; }
  .label__band { position: absolute; left: 0; top: 194px; width: 1200px; height: 240px; }

  .storage { position: absolute; left: 34px; top: 36px; width: 297px; font: 600 20.5px/1.45 var(--font-text); text-align: justify; text-align-last: left; }
  .storage p + p { margin-top: 8px; }

  .brand { position: absolute; left: 400px; width: 400px; top: 36px; text-align: center; font: 400 34px/1 var(--font-text); letter-spacing: 0.22em; padding-left: 0.22em; }
  .brand__rule { position: absolute; left: 525px; top: 91px; width: 153px; height: 3px; background: var(--tomato); }

  .product-name { position: absolute; left: 400px; width: 400px; text-align: center; font-family: var(--font-title); line-height: 1; letter-spacing: -1px; }
  .product-name--tomato { top: 118px; font-size: 76px; color: var(--ink); text-shadow: 5px 3px 0 var(--tomato); }
  .product-name--ketchup { top: 208px; font-size: 74px; color: var(--cream); text-shadow: -5px 3px 0 var(--ink); }

  .ribbon-art { position: absolute; left: 452px; top: 296px; width: 307px; height: 104px; border-radius: 8px;
    background: linear-gradient(180deg, rgba(230,220,199,0.55) 0%, rgba(230,220,199,0.85) 100%); }

  .title { position: absolute; left: 834px; top: 30px; width: 350px; font: 24px/1.18 var(--font-label); color: var(--tomato); letter-spacing: 0.04em; }
  .ingredients { position: absolute; left: 834px; top: 99px; width: 360px; font: 600 19.6px/1.35 var(--font-text); }

  .maker { position: absolute; left: 32px; top: 224px; font: 400 19px/1.35 var(--font-text); color: var(--cream); }
  .web { position: absolute; left: 32px; top: 383px; font: 19px/1 var(--font-label); color: var(--cream); letter-spacing: 0.08em; }

  .vegan-mark { position: absolute; left: 842px; top: 304px; width: 90px; height: 60px; }
  .weight { position: absolute; left: 830px; top: 383px; font: 400 19px/1 var(--font-text); color: var(--cream); }
  .info-box { position: absolute; left: 978px; top: 300px; width: 187px; height: 99px; background: var(--cream); }
</style>
</head>
<body>
<main class="label">
  <svg class="label__band" viewBox="0 0 1200 240" aria-hidden="true">
    <defs>
      <pattern id="zigzag" width="13.6" height="8" patternUnits="userSpaceOnUse">
        <polygon points="0,8 6.8,0 13.6,8" fill="#ee4758"/>
      </pattern>
    </defs>
    <rect x="0" y="0" width="1200" height="8" fill="url(#zigzag)"/>
    <rect x="0" y="8" width="1200" height="232" fill="#ee4758"/>
  </svg>

  <section class="storage">
    <p>Nach dem Öffnen gekühlt aufbewahren und rasch konsumieren.</p>
    <p>Pasteurisiert.</p>
  </section>

  <div class="brand">BLUE FERN</div>
  <div class="brand__rule"></div>

  <h1 class="product-name product-name--tomato">TOMATO</h1>
  <div class="product-name product-name--ketchup">KETCHUP</div>

  <div class="ribbon-art" role="img" aria-label="Illustration of tomatoes above a ribbon banner reading Handcrafted"></div>

  <h2 class="title">HANDCRAFTED TOMATO KETCHUP</h2>
  <p class="ingredients">Tomaten, Weissweinessig, Aceto Balsamico, brauner Rohrzucker, Maisstärke, Gewürze, Salz</p>

  <p class="maker">Handcrafted in Switzerland by<br>Varentoli Kulina GmbH, Chur</p>
  <p class="web">WWW.BLUEFERN-VOREL.EXAMPLE</p>

  <svg class="vegan-mark" viewBox="0 0 90 60" role="img" aria-label="Vegan badge">
    <path d="M45 3 C70 3 87 14 87 30 C87 46 70 57 45 57 C20 57 3 46 3 30 C3 14 20 3 45 3 Z" fill="none" stroke="#e6dcc7" stroke-width="2.5"/>
  </svg>
  <p class="weight">200 Gramm</p>
  <div class="info-box"></div>
</main>
</body>
</html>
```